New Company Business Card design

Looking for a corporate looking business card utilising my new logo design - the logo i would like embossed as one option and flat as another - simplistic but stylish - less is more - we are an import export business launching into the market - i would like a couple of options as main background - Grey or Black

```html
<!DOCTYPE html>
<html lang="en">
<head>
<meta charset="utf-8">
<title>Meridian Trade Partners – Business Card</title>
<link href="https://fonts.googleapis.com/css2?family=Lato:wght@400;700&display=swap" rel="stylesheet">
<style>
  :root {
    --stage: #2b2b2d;
    --card: #1c1d20;
    --blue: #1f7bd1;
    --grey: #7a7a7e;
    --white: #f2f2f2;
    --rule: #6d6e72;
  }
  html, body {
    margin: 0;
    width: 1200px;
    height: 1108px;
    overflow: hidden;
    background: var(--stage);
    font-family: "Lato", Arial, sans-serif;
  }
  .stage {
    position: relative;
    width: 1200px;
    height: 1108px;
    display: flex;
    justify-content: center;
    align-items: center;
    gap: 80px;
  }
  .card {
    position: relative;
    width: 400px;
    height: 640px;
    background: var(--card);
    border-radius: 22px;
    box-shadow: 0 14px 34px rgba(0,0,0,.45);
    box-sizing: border-box;
    display: flex;
    flex-direction: column;
    align-items: center;
    text-align: center;
  }
  .brand {
    display: flex;
    align-items: center;
    gap: 12px;
    color: var(--blue);
    font-weight: 700;
    font-size: 21px;
    letter-spacing: 1.5px;
    text-transform: uppercase;
  }
  .brand-dot {
    width: 30px;
    height: 30px;
    border-radius: 50%;
    background: var(--blue);
    flex: none;
  }
  .card-front { padding-top: 120px; }
  .person-name {
    margin: 92px 0 0;
    color: var(--blue);
    font-size: 27px;
    font-weight: 400;
    letter-spacing: .5px;
    text-transform: uppercase;
  }
  .person-role {
    margin: 4px 0 0;
    color: var(--white);
    font-size: 19px;
  }
  .icon-rule {
    margin-top: 26px;
    display: flex;
    align-items: center;
    gap: 8px;
  }
  .icon-rule .line { width: 64px; height: 1px; background: var(--rule); }
  .icon-rule svg { width: 22px; height: 22px; display: block; }
  .contacts {
    margin-top: 12px;
    color: var(--white);
    font-size: 20px;
    line-height: 1.3;
  }
  .contacts p { margin: 0; }
  .divider {
    width: 230px;
    height: 1px;
    background: var(--rule);
    margin: 14px 0 10px;
  }
  .card-back { justify-content: center; }
  .back-web {
    position: absolute;
    bottom: 58px;
    left: 0;
    right: 0;
    color: var(--blue);
    font-family: "Lato", Arial, sans-serif;
    font-size: 19px;
    letter-spacing: 2px;
  }
</style>
</head>
<body>
<main class="stage">
  <section class="card card-front">
    <div class="brand"><span class="brand-dot"></span>Meridian Trade Partners</div>
    <h1 class="person-name">Daniel Marsh</h1>
    <p class="person-role">Managing Director</p>
    <div class="icon-rule">
      <span class="line"></span>
      <svg viewBox="0 0 22 22" aria-label="phone"><circle cx="11" cy="11" r="11" fill="var(--blue)"/><path d="M8 6.5c.6 0 1.6 2.2 1.3 2.7l-.8.9c.6 1.3 1.5 2.2 2.8 2.8l.9-.8c.5-.3 2.7.7 2.7 1.3 0 .9-1 2-2 2C9.5 15.4 6.6 12.5 6 8.5c0-1 1.1-2 2-2z" fill="var(--card)"/></svg>
      <svg viewBox="0 0 22 22" aria-label="email"><circle cx="11" cy="11" r="11" fill="var(--blue)"/><rect x="6" y="7.5" width="10" height="7" rx="1" fill="var(--card)"/><path d="M6.5 8l4.5 3.5L15.5 8" stroke="var(--blue)" stroke-width="1" fill="none"/></svg>
      <svg viewBox="0 0 22 22" aria-label="website"><circle cx="11" cy="11" r="11" fill="var(--blue)"/><circle cx="11" cy="11" r="5" fill="none" stroke="var(--card)" stroke-width="1.4"/><path d="M6 11h10M11 6c-2.5 3-2.5 7 0 10M11 6c2.5 3 2.5 7 0 10" fill="none" stroke="var(--card)" stroke-width="1.1"/></svg>
      <span class="line"></span>
    </div>
    <div class="contacts">
      <p>444 555 7120</p>
      <p>hello@meridiantrade.com</p>
      <p>www.meridiantrade.com</p>
    </div>
    <div class="divider"></div>
    <div class="contacts">
      <p>38 Harbour Road,</p>
      <p>Portside, 20817</p>
    </div>
  </section>

  <section class="card card-back">
    <div class="brand"><span class="brand-dot"></span>Meridian Trade Partners</div>
    <p class="back-web">www.meridiantrade.com</p>
  </section>
</main>
</body>
</html>
```